Computer business require Thank you flyer to include in shipments

We ship computers (mainly laptops, tablets) to customers, most shipments are single unit in a box, we like to include in each box one page flyer as a Thank you note, and also mention in the note that for any reason if the buyer is not satisfied with the purchase or they wish to return the item they can contact us and will take care of any issue.
am thinking to have the design reflect a modern look, also with some color possibly to attract the customer attention and make them read the note, as some people tend to not read paper included in shipments. I will include the content that we like to be on the flyer, however we are open to suggestions either to add more text or how to layout the contents on the page. We also have a company logo that we would like to have it on the flyer.

Target Market(s)

End user, business buyers, wholesalers

Industry/Entity Type

Business

Font styles to use
Sans Serif
Other font styles liked:
• maybe even arial or times roman, a font that would be commonly used for a flyer easy readable

Colors
3377b5
f04a50
e667a6
b868aa
33a6d7
0792cd
ec1f27

Requirements
Must have
• Company logo
Nice to have
• Possible the address somewhere on the bottom of the page either left or right or one line at the end, depending how would look with the layout.
• Not too sure about color, most likely blue similar to our logo colors would be first choice, I was also thinking just to catch buyers attention when they open the package should we do it maybe red or even pink which would be softer tone possibly making it interesting for buyer to read. I know some colors would bring more attention to say "READ ME". Or maybe I'll have 2 flyers in different colors and sent to buyers accordingly based on the gender.
Should not have
• Somehow I did not realize we had added the note section on the content, I like to remove that part that mention about "Read Below Notes...." then the two paragraph that follow about technical guide. I just want this flyer be a Thank you note as well as inform buyers to contact us directly if they have issue.

```html
<!DOCTYPE html>
<html lang="en">
<head>
<meta charset="utf-8">
<title>Veltrix Global – Thank You</title>
<link rel="stylesheet" href="https://fonts.googleapis.com/css2?family=Open+Sans:wght@300;400;600;700&display=swap">
<style>
:root{
  --blue:#3377b5;
  --blue-deep:#0792cd;
  --blue-light:#33a6d7;
  --ink:#3d4650;
  --muted:#5a636c;
  --pale:#e8f1f8;
  --white:#ffffff;
}
*{margin:0;padding:0;box-sizing:border-box}
html,body{width:849px;height:1200px;overflow:hidden;background:var(--white)}
body{font-family:"Open Sans",Arial,sans-serif;color:var(--ink)}
.flyer{position:relative;width:849px;height:1200px;overflow:hidden;
  background:linear-gradient(180deg,var(--white) 40%,var(--pale) 100%)}
.hero-photo{position:absolute;left:0;top:0;width:849px;height:500px;
  background:
    radial-gradient(ellipse 260px 200px at 560px 230px,rgba(214,180,160,.55),rgba(214,180,160,0) 70%),
    radial-gradient(ellipse 200px 170px at 330px 300px,rgba(120,150,190,.45),rgba(120,150,190,0) 70%),
    radial-gradient(ellipse 180px 160px at 760px 170px,rgba(200,175,150,.45),rgba(200,175,150,0) 70%),
    linear-gradient(180deg,#f3f5f7 0%,#e7ebef 55%,#f7f8f9 100%)}
.brand{position:absolute;left:44px;top:40px;display:flex;align-items:center;gap:12px}
.brand-mark{width:34px;height:34px;border-radius:50%;background:var(--blue-light)}
.brand-name{font-size:32px;font-weight:700;color:var(--blue);letter-spacing:1px;line-height:1}
.brand-tag{position:absolute;left:44px;top:84px;font-size:12px;color:var(--muted)}
.headline{position:absolute;left:44px;top:262px;font-size:54px;font-weight:300;color:var(--blue);letter-spacing:1px;line-height:1}
.wave{position:absolute;left:0;top:410px;width:849px;height:110px}
.letter{position:absolute;left:70px;top:540px;width:712px;font-size:14.5px;line-height:1.6}
.letter p{margin-bottom:18px}
.highlight{color:var(--blue);font-weight:700}
.footer{position:absolute;left:0;top:1130px;width:849px;height:70px;background:var(--blue);color:var(--white);text-align:center;font-size:13px;padding-top:14px;line-height:1.65}
</style>
</head>
<body>
<div class="flyer">
  <div class="hero-photo" role="img" aria-label="Photo of a smiling family relaxing together on a white sofa with a laptop"></div>

  <div class="brand">
    <span class="brand-mark"></span>
    <span class="brand-name">VELTRIX GLOBAL</span>
  </div>
  <div class="brand-tag">Computer &amp; Electronics Wholesaler</div>

  <h1 class="headline">THANK YOU</h1>

  <svg class="wave" viewBox="0 0 849 110" preserveAspectRatio="none" aria-hidden="true">
    <path d="M0 40 C220 90 520 10 849 55 L849 110 L0 110 Z" fill="var(--blue-light)" opacity=".55"/>
    <path d="M0 60 C260 105 560 30 849 70 L849 110 L0 110 Z" fill="var(--blue)"/>
    <path d="M0 88 C280 120 560 60 849 92 L849 110 L0 110 Z" fill="var(--white)"/>
  </svg>

  <section class="letter">
    <p>Dear Customer,</p>
    <p>Thank you for your purchase.</p>
    <p>We very much appreciate your business. It has been a pleasure serving you.<br>
    <span class="highlight">Customer satisfaction is our #1 priority</span> at the same time our commitment is to provide quality products with exceptional customer service.</p>
    <p>We hope you have received your item in good condition and in a timely manner.</p>
    <p>Please keep the original packaging just in case you would require to return the item. We respectfully ask if you are in any way unhappy with your purchase, either having remorse, change of mind or an issue with the item received even during warranty period, please contact us directly via email at support@veltrixglobal.com or call us Toll Free at (888) 555-0147 during business hours Monday - Friday, 9am to 4pm PST and give us the opportunity to make it right for you, we are committed to ensuring that you are completely satisfied with your purchase, appreciate your patience until we solve any issue, we value your business and would like to address your concern as quickly as possible.</p>
    <p>If you have been satisfied with our product and service we would greatly appreciate a moment of your time to leave your positive feedback for this transaction on the website of purchase, your opinion would allow us to maintain our high standards in providing a wonderful buying experience for all customers.</p>
  </section>

  <footer class="footer">
    sales@veltrixglobal.com &nbsp;|&nbsp; www.veltrixglobal.com &nbsp;|&nbsp; Toll Free : 1-888-555-0147<br>
    2240 N. Harbor Ave., Fairview, CA 90000
  </footer>
</div>
</body>
</html>
```